The design should look similar to the uploaded example to accommodate the information needed for a business card template. I would like to see the colors orange and charcoal grey incorporated along with the logo.The following should be on the back of the card SPECIALIZING IN NEW AND USED TIRES & WHEELS FOR:- Loaders- Skid Steers- Telehandlers- Boom Lifts- Forklifs and moreELIMINATING DOWNTIMEWheel Exchange Program for New & Used Foam Filled and Solid Rubber TiresSPECIALTY SERVICES- Foam Filling Tires- Largest Tire Press in SE- ONSITE Forklift Tire Press- Boom Truck Services - Rubber Tracks

Target Market(s)

New and Existing Customers

Industry/Entity Type

Business

Contact Information for Business Card

NAMEHEAVY DUTY TIRE, LLC8470 Belvedere RoadWest Palm Beach, FL 33411P: 844-HD-TIRESF: 561-431-6469C:E: W: WWW.GRANITERIMSUPPLY-EXAMPLE.COM

Font styles to use
Sans Serif

Colors
f37122
333333

Requirements
Must have
• The logo and the information indicated for the backside of the card
Nice to have
• Keep the orange and charcoal grey colors

```html
<!DOCTYPE html>
<html lang="en">
<head>
<meta charset="utf-8">
<title>Granite Rim Supply — Business Card</title>
<link rel="stylesheet" href="https://fonts.googleapis.com/css2?family=Roboto:wght@400;500;700;900&display=swap">
<style>
  :root {
    --orange: #f37122;
    --charcoal: #333333;
    --slate: #3e4852;
    --slate-dark: #2c343c;
    --paper: #ffffff;
    --ink: #3a3a3a;
    --muted: #5b6169;
    --backdrop: #e9e6e1;
  }
  * { box-sizing: border-box; margin: 0; padding: 0; }
  html, body {
    width: 1200px; height: 950px; overflow: hidden;
    background: var(--backdrop);
    font-family: "Roboto", Arial, sans-serif;
  }
  .stage { position: relative; width: 1200px; height: 950px; }
  .card {
    position: absolute; left: 240px; width: 720px; height: 411px;
    border-radius: 6px; overflow: hidden;
    box-shadow: 0 10px 28px rgba(0,0,0,.22);
  }
  /* back side */
  .card--back {
    top: 48px;
    background: linear-gradient(160deg, var(--slate) 0%, var(--slate-dark) 100%);
    color: #fff; padding: 42px 48px;
  }
  .brand { display: flex; align-items: center; gap: 18px; }
  .brand__dot {
    width: 64px; height: 64px; border-radius: 50%;
    background: var(--orange); flex: none;
  }
  .brand__name {
    font-weight: 900; font-size: 34px; line-height: 1.02;
    text-transform: uppercase; letter-spacing: .5px;
  }
  .card--back .brand__name { color: #fff; }
  .services { margin-top: 30px; }
  .services h3 {
    font-size: 17px; font-weight: 700; text-transform: uppercase;
    letter-spacing: .4px; margin-top: 16px;
  }
  .services h3:first-child { margin-top: 0; }
  .services p { font-size: 15px; margin-top: 5px; color: #e4e8ec; line-height: 1.4; }
  .bullet { color: var(--orange); font-weight: 700; padding: 0 6px; }

  /* front side */
  .card--front { top: 489px; background: var(--paper); color: var(--ink); }
  .card--front .brand { position: absolute; left: 190px; top: 48px; }
  .card--front .brand__dot { width: 96px; height: 96px; }
  .card--front .brand__name { color: var(--charcoal); font-size: 38px; }
  .person { position: absolute; left: 60px; top: 186px; text-align: right; width: 250px; }
  .person__name { font-size: 24px; font-weight: 500; color: var(--charcoal); }
  .person__title { font-size: 17px; color: var(--orange); margin-top: 2px; }
  .person__addr { font-size: 16px; color: var(--muted); margin-top: 8px; line-height: 1.35; }
  .divider {
    position: absolute; left: 335px; top: 186px; width: 1px; height: 118px;
    background: #c9cdd2;
  }
  .contacts { position: absolute; left: 358px; top: 184px; list-style: none; }
  .contacts li {
    display: flex; align-items: center; gap: 12px;
    font-size: 17px; color: var(--ink); height: 29px;
  }
  .contacts svg { width: 16px; height: 16px; fill: var(--slate); flex: none; }
  .swoosh { position: absolute; left: 0; bottom: 0; width: 720px; height: 110px; }
  .website {
    position: absolute; left: 70px; bottom: 22px;
    color: #fff; font-size: 17px; letter-spacing: 2px;
  }
</style>
</head>
<body>
<main class="stage">

  <section class="card card--back" aria-label="Card back">
    <div class="brand">
      <span class="brand__dot"></span>
      <h2 class="brand__name">Granite Rim<br>Supply LLC</h2>
    </div>
    <div class="services">
      <h3>Specializing in new and used tires &amp; wheels for</h3>
      <p>Loaders<span class="bullet">•</span>Skid Steers<span class="bullet">•</span>Telehandlers<span class="bullet">•</span>Boom Lifts<span class="bullet">•</span>Forklifts and more</p>
      <h3>Eliminating downtime</h3>
      <p>Wheel Exchange Program for New &amp; Used Foam Filled and Solid Rubber Tires</p>
      <h3>Specialty services</h3>
      <p>Foam Filling Tires<span class="bullet">•</span>Largest Tire Press in SE<span class="bullet">•</span>ONSITE Forklift Tire Press<br>Boom Truck Services<span class="bullet">•</span>Rubber Tracks</p>
    </div>
  </section>

  <section class="card card--front" aria-label="Card front">
    <div class="brand">
      <span class="brand__dot"></span>
      <h1 class="brand__name">Granite Rim<br>Supply LLC</h1>
    </div>

    <div class="person">
      <p class="person__name">Dana Whitlock</p>
      <p class="person__title">President</p>
      <p class="person__addr">5126 Marston Lane<br>West Palm Beach, FL 33411</p>
    </div>
    <span class="divider"></span>
    <ul class="contacts">
      <li><svg viewBox="0 0 16 16"><path d="M2 5c0-2 2-3 6-3s6 1 6 3v1h-3V5H5v1H2zM3 8h10l1 6H2zm5 1.5a2 2 0 100 4 2 2 0 000-4z"/></svg>844-GR-WHEEL</li>
      <li><svg viewBox="0 0 16 16"><path d="M4 1h8v14H4zm1.5 1.5v10h5v-10zM7 13.2h2v1H7z"/></svg>836 512 7740</li>
      <li><svg viewBox="0 0 16 16"><path d="M4 1h7v4H4zM2 6h12v6h-2v3H4v-3H2zm3 4v4h6v-4z"/></svg>561-278-9053</li>
      <li><svg viewBox="0 0 16 16"><path d="M1 3h14v10H1zm1.5 1.4V5l5.5 4 5.5-4v-.6z"/></svg>dana@graniterimsupply-example.com</li>
    </ul>

    <svg class="swoosh" viewBox="0 0 720 110" preserveAspectRatio="none" aria-hidden="true">
      <path d="M0 30 C 220 62, 480 78, 720 70 L720 110 L0 110 Z" fill="#f37122"/>
      <path d="M0 38 C 220 70, 480 86, 720 78 L720 110 L0 110 Z" fill="#3e4852"/>
    </svg>
    <p class="website">www.graniterimsupply-example.com</p>
  </section>

</main>
</body>
</html>
```